Vitamin B12 Liquid Drops Label

hi, i need a label designed for my vitamin b12 drops that i am going to be selling on shopzello. the label needs to quickly capture the attention of a buyer as he or she is scrolling through the thumbnail search results on shopzello.com my brand is called nralo. i already have an example brand logo i will be using, however, i need help designing the rest of the label. attached are some examples of labels i like for other supplements.some of these examples are pink. i do not want pink. please go for a blue/green color scheme. THE DESIGN MUST BE BOLD

Target Market(s)

adults ages 30 - 64

Font styles to use
Sans Serif

Colors
0455a3
cedeed
3176b5
85acd3
cfdeed
9bcb3b
abd037
cadf82
00a990

Requirements
Must have
• - bold design
• - somewhat gender-neutral color scheme because this will be used equally by men and women
• - B12 MUST be very prominent and visible on the label
Should not have
• - it should not be "crunchy" looking

```html
<!DOCTYPE html>
<html lang="en">
<head>
<meta charset="utf-8">
<title>nralo Vitamin B12 Drops Label</title>
<link rel="stylesheet" href="https://fonts.googleapis.com/css2?family=PT+Sans:wght@700&display=swap">
<style>
  :root {
    --backdrop: #1a17a6;
    --label-blue: #2b35e2;
    --label-gold: #f5ac2c;
    --title-blue: #1c1ec8;
    --accent-gold: #f1b031;
  }
  html, body {
    margin: 0;
    padding: 0;
    overflow: hidden;
  }
  body {
    width: 1200px;
    height: 900px;
    background: var(--backdrop);
    font-family: "PT Sans", sans-serif;
  }
  .label {
    position: absolute;
    left: 318px;
    top: 80px;
    width: 564px;
    height: 724px;
    display: block;
  }
  .label-base { fill: var(--label-blue); }
  .label-band { fill: var(--label-gold); }
  .product-name {
    fill: var(--title-blue);
    font-family: "PT Sans", sans-serif;
    font-weight: 700;
    font-size: 31px;
    letter-spacing: 0.5px;
  }
  .ingredient {
    fill: var(--accent-gold);
    font-family: "PT Sans", sans-serif;
    font-weight: 700;
    font-size: 10px;
    letter-spacing: 4px;
  }
  .brand-name {
    fill: var(--accent-gold);
    font-family: "PT Sans", sans-serif;
    font-weight: 700;
    font-size: 34px;
  }
</style>
</head>
<body>
  <svg class="label" viewBox="0 0 300 385" role="group" aria-label="nralo Vitamin B12 methylcobalamin drops label">
    <rect class="label-base" x="0" y="0" width="300" height="385"/>
    <polygon class="label-band" points="0,0 300,0 226,202 0,202"/>
    <text class="product-name" x="10" y="196">VITAMIN B12</text>
    <text class="ingredient" x="14" y="226">METHYLCOBAMALIN</text>
    <text class="brand-name" x="288" y="350" text-anchor="end">nralo</text>
  </svg>
</body>
</html>
```